Upmarket Dessert Lounge needs a Business Card Design

We are an upmarket dessert lounge needing a business card to match our image.

We want something that is simple yet beautiful, feminine, classy, sophisticated and elegant. We want it to stand out and don't mind if it is bold.

The design should include our logo and colours of red or maroon with gold highlights. We don't mind if black is used.

Marlow & Quince

Target Market(s)

For those who like to indulge or treat themselves and give in to their temptations on good quality desserts.

Industry/Entity Type

Business

Requirements
Must have
• Must include our logo and our name

Marlow & Quince

M & Q

```html
<!DOCTYPE html>
<html lang="en">
<head>
<meta charset="utf-8">
<title>Marlow &amp; Quince — Business Card</title>
<link rel="stylesheet" href="https://fonts.googleapis.com/css2?family=Tinos:wght@400;700&display=swap">
<style>
  :root {
    --backdrop: #d8cbbd;
    --card-navy: #050d24;
    --maroon: #8a1a1c;
    --gold: #f1cd8e;
    --ivory: #f4efe6;
    --divider: #8c8f9c;
  }
  * { box-sizing: border-box; margin: 0; padding: 0; }
  html, body {
    width: 1200px; height: 417px; overflow: hidden;
    background: var(--backdrop);
    font-family: "Tinos", "Times New Roman", serif;
  }
  .stage { position: relative; width: 1200px; height: 417px; }
  .card {
    position: absolute; top: 62px; width: 514px; height: 292px;
    background: var(--card-navy); border-radius: 14px; color: var(--ivory);
  }
  .card--front { left: 55px; }
  .card--back { left: 630px; }

  .holder {
    position: absolute; top: 26px; left: 0; right: 0; text-align: center;
    color: var(--gold);
  }
  .holder__name { font-weight: 700; font-size: 17px; letter-spacing: 0.3px; }
  .holder__title { font-size: 13px; }

  .brand {
    position: absolute; left: 0; right: 0;
    display: flex; align-items: center; justify-content: center; gap: 12px;
  }
  .card--front .brand { top: 110px; }
  .card--back .brand { top: 104px; }
  .brand__seal {
    width: 50px; height: 50px; border-radius: 50%;
    background: var(--maroon); flex: none;
  }
  .brand__name {
    color: var(--gold); font-size: 27px; letter-spacing: 0.5px;
    text-transform: uppercase; white-space: nowrap;
  }

  .contact {
    position: absolute; top: 236px; left: 0; right: 0;
    font-size: 13px; line-height: 19px;
  }
  .contact__col { position: absolute; top: 0; }
  .contact__col--address { left: 51px; }
  .contact__col--phones { left: 192px; }
  .contact__col--online { left: 343px; }
  .contact__divider {
    position: absolute; top: 1px; width: 1px; height: 37px; background: var(--divider);
  }
  .contact__divider--one { left: 181px; }
  .contact__divider--two { left: 332px; }
  .contact__line { display: flex; align-items: center; gap: 6px; white-space: nowrap; }
  .contact__icon { width: 9px; height: 9px; fill: var(--gold); flex: none; }

  .back-web {
    position: absolute; top: 220px; left: 0; right: 0; text-align: center;
    font-size: 15px; letter-spacing: 3.2px; color: var(--ivory);
  }
</style>
</head>
<body>
<main class="stage">
  <section class="card card--front" aria-label="Business card front">
    <p class="holder"><span class="holder__name">YOUR NAME,</span> <span class="holder__title">Title</span></p>
    <div class="brand">
      <span class="brand__seal" aria-hidden="true"></span>
      <p class="brand__name">Marlow &amp; Quince</p>
    </div>

    <div class="contact">
      <div class="contact__col contact__col--address">
        <p>00, Complex name</p>
        <p>City, State 000 000</p>
      </div>
      <span class="contact__divider contact__divider--one"></span>
      <div class="contact__col contact__col--phones">
        <p class="contact__line">
          <svg class="contact__icon" viewBox="0 0 10 10" aria-hidden="true"><path d="M2 0.5 L3.6 2.6 L2.7 3.6 Q3.8 5.9 6.3 7.2 L7.4 6.3 L9.5 7.9 L8.3 9.5 Q1.2 8 0.5 1.7 Z"/></svg>
          +2348120453318
        </p>
        <p class="contact__line">
          <svg class="contact__icon" viewBox="0 0 10 10" aria-hidden="true"><path d="M2.5 0 H7.5 V10 H2.5 Z M3.4 1 V7.6 H6.6 V1 Z"/><circle cx="5" cy="8.8" r="0.6"/></svg>
          +2348120453318
        </p>
      </div>
      <span class="contact__divider contact__divider--two"></span>
      <div class="contact__col contact__col--online">
        <p class="contact__line">
          <svg class="contact__icon" viewBox="0 0 10 10" aria-hidden="true"><path d="M0.5 2 H9.5 V8 H0.5 Z"/><path d="M0.5 2 L5 5.5 L9.5 2" fill="none" stroke="#050d24" stroke-width="0.8"/></svg>
          info@marlowquince.com
        </p>
        <p class="contact__line">
          <svg class="contact__icon" viewBox="0 0 10 10" aria-hidden="true"><circle cx="5" cy="5" r="4.5"/><path d="M0.5 5 H9.5 M5 0.5 Q2.5 5 5 9.5 M5 0.5 Q7.5 5 5 9.5" fill="none" stroke="#050d24" stroke-width="0.7"/></svg>
          www.marlowquince.com
        </p>
      </div>
    </div>
  </section>

  <section class="card card--back" aria-label="Business card back">
    <div class="brand">
      <span class="brand__seal" aria-hidden="true"></span>
      <p class="brand__name">Marlow &amp; Quince</p>
    </div>
    <p class="back-web">www.marlowquince.com</p>
  </section>
</main>
</body>
</html>
```